Panty packaging

what we are looking for is 1 of a kind packaging for women's panties. It should have the same theme for all styles but a different outline or a color code setting the difference between styles. Most company's are packaging in a poly bag or hanger, what we are looking for is a box packaging. also customer should be able to see whats in the box without having to open the box. If there are different colors, the window should show that. We want to be able to customize the design for different styles and for 1 color package or multi color package. It should be sleek and sophisticated. Box does not have to be square, it can have curved edges or be totally round, the most important thins is that it should be stack-able. Sometimes the box will hold a pack of 3 and sometimes a single item, so box height may vary. We need a graphic on the box to indicate the style, for example: hipster, brief, hi cut, or lo cut. box needs a space to put a small size chart. Out logo can be color changed to match theme and background colors, just stick with the 3 colors, black, white, and magneta.
Female market all ages. upscale market
It Company

```html
<!DOCTYPE html>
<html lang="en">
<head>
<meta charset="utf-8">
<title>Velmora – Box Packaging</title>
<link rel="stylesheet" href="https://fonts.googleapis.com/css2?family=Lato:wght@300&family=Pinyon+Script&display=swap">
<style>
  :root {
    --ink: #0b0909;
    --sleeve: #151314;
    --sleeve-edge: #232022;
    --magenta: #c4117e;
    --magenta-deep: #9c0c63;
    --gold: #c9a21c;
    --gold-light: #f0d24a;
    --window: #b9d3bd;
    --window-light: #d6e7d8;
    --white: #ffffff;
    --tab: #2a1c22;
  }
  * { margin: 0; padding: 0; box-sizing: border-box; }
  html, body { width: 1200px; height: 818px; overflow: hidden; background: var(--ink); }
  .canvas {
    position: relative;
    width: 1200px;
    height: 818px;
    background: radial-gradient(ellipse at 45% 40%, #1f1a1a 0%, var(--ink) 70%);
  }
  .brand {
    position: absolute;
    top: 92px;
    left: 790px;
    width: 240px;
    text-align: center;
  }
  .brand-name {
    font-family: "Lato", sans-serif;
    font-weight: 300;
    font-size: 48px;
    letter-spacing: 2px;
    color: var(--white);
    line-height: 1;
  }
  .tagline {
    margin-top: 30px;
    font-family: "Pinyon Script", cursive;
    font-size: 26px;
    color: var(--white);
    white-space: nowrap;
    letter-spacing: 1px;
  }
  .box {
    position: absolute;
    left: 150px;
    top: 360px;
    width: 900px;
  }
  .box-top {
    position: relative;
    height: 250px;
    display: flex;
  }
  .sleeve-end {
    width: 160px;
    background: var(--sleeve);
    border-right: 12px solid var(--gold);
  }
  .top-main {
    flex: 1;
    display: flex;
    flex-direction: column;
  }
  .sleeve-band {
    height: 72px;
    background: var(--sleeve);
    display: flex;
    align-items: center;
    justify-content: center;
    padding-right: 160px;
  }
  .sleeve-name {
    font-family: "Lato", sans-serif;
    font-weight: 300;
    font-size: 24px;
    letter-spacing: 2px;
    color: var(--white);
  }
  .gold-band {
    height: 12px;
    background: linear-gradient(90deg, var(--gold), var(--gold-light), var(--gold));
  }
  .window {
    flex: 1;
    background: linear-gradient(100deg, var(--window) 0%, var(--window-light) 45%, var(--window) 100%);
    border: 10px solid var(--magenta);
    border-top: none;
  }
  .box-front {
    position: relative;
    height: 80px;
    display: flex;
  }
  .front-sleeve {
    width: 160px;
    background: var(--sleeve-edge);
    border-right: 12px solid var(--gold);
  }
  .front-tray {
    flex: 1;
    background: linear-gradient(180deg, var(--magenta) 0%, var(--magenta-deep) 100%);
    position: relative;
  }
  .pull-tab {
    position: absolute;
    left: 50%;
    top: -8px;
    width: 16px;
    height: 34px;
    margin-left: -8px;
    background: var(--tab);
    border-radius: 2px;
  }
</style>
</head>
<body>
<main class="canvas">
  <header class="brand">
    <div class="brand-name">VELMORA</div>
    <p class="tagline">For your special night</p>
  </header>

  <section class="box" aria-label="Box with sliding tray">
    <div class="box-top">
      <div class="sleeve-end"></div>
      <div class="top-main">
        <div class="sleeve-band"><span class="sleeve-name">VELMORA</span></div>
        <div class="gold-band" role="img" aria-label="Gold patterned trim band"></div>
        <div class="window" role="img" aria-label="Clear window showing folded panties inside"></div>
      </div>
    </div>
    <div class="box-front">
      <div class="front-sleeve"></div>
      <div class="front-tray"><span class="pull-tab"></span></div>
    </div>
  </section>
</main>
</body>
</html>
```